Visitenkarten und Briefpapier
Zielgruppe
Planung und Realisierung von individuellen und wertbeständigen Kamin- und Ofenlösungen, sowie Fliesen- und Baddesign.
Aufgabenstellung
Wir benötigen ein möglichst schlichtes Design für Visitenkarten, bzw. Briefpapier. Für die Visitenkarten gerne auch Vorschläge mit Prägung, Ausstanzung oder mit Heißfolie. Auch Klappkarten wären denkbar. Das Design soll "das gewisse Etwas haben" und nicht zu verspielt sein.
Die Visitenkarten sind für die Firma KORVA, das Logo von der Ausstellung "raumfunke" soll dezent mit eingebunden werden (bei dem Briefpapier z.B. in der Fußzeile". Die farbliche Gestaltung sollte sich an den Farben des Logos orientieren.
Schriftart für Texte: Century Gothic
Schriftfarbe: RAL 7016
Nur eine Idee: Ich könnte mir auch gut vorstellen, dass die Visitenkarte aus einer Zündholzverpackung (wenn dann aber eine besondere mit nur einem Zündholz oder einem besonders breiten) besteht: http://glimmvelo.de/produkte_briefchen.php

```html
<!DOCTYPE html>
<html lang="de">
<head>
<meta charset="utf-8">
<title>KORVA – Visitenkarte</title>
<link href="https://fonts.googleapis.com/css2?family=Questrial&display=swap" rel="stylesheet">
<style>
  :root {
    --backdrop: #c89e69;
    --card: #24343b;
    --text: #c6c6c6;
    --font: "Questrial", sans-serif;
  }
  html, body {
    margin: 0;
    padding: 0;
    width: 1200px;
    height: 1120px;
    overflow: hidden;
    background: var(--backdrop);
  }
  .business-card {
    position: absolute;
    left: 274px;
    top: 101px;
    width: 602px;
    height: 390px;
    background: var(--card);
    color: var(--text);
    font-family: var(--font);
  }
  .brand {
    position: absolute;
    left: 22px;
    top: 22px;
  }
  .brand-name {
    margin: 0;
    font-size: 84px;
    line-height: 1;
    font-weight: 400;
    letter-spacing: 4px;
  }
  .brand-tagline {
    margin: 4px 0 0 2px;
    font-size: 25px;
    line-height: 1.1;
  }
  .person {
    position: absolute;
    left: 23px;
    top: 210px;
  }
  .person-name {
    margin: 0;
    font-size: 34px;
    line-height: 1.1;
    font-weight: 400;
  }
  .person-role {
    margin: 2px 0 0 0;
    font-size: 15px;
  }
  .website {
    position: absolute;
    left: 17px;
    top: 348px;
    font-size: 18.5px;
  }
  .contact {
    position: absolute;
    right: 17px;
    top: 256px;
    text-align: right;
    font-size: 18.5px;
    line-height: 22.5px;
    font-style: normal;
  }
  .contact .label {
    display: inline-block;
    margin-right: 14px;
  }
  .contact .mail {
    margin-top: 2px;
  }
</style>
</head>
<body>
  <section class="business-card">
    <header class="brand">
      <h1 class="brand-name">KORVA</h1>
      <p class="brand-tagline">kamine · öfen · fliesen</p>
    </header>

    <div class="person">
      <h2 class="person-name">Jonas Keller</h2>
      <p class="person-role">Geschäftsführer</p>
    </div>

    <div class="website">www.korva-talbrunn.de</div>

    <address class="contact">
      <div>Am Lindenweg 4c</div>
      <div>35012 Talbrunn</div>
      <div><span class="label">fon:</span>04711 / 38 19 40</div>
      <div><span class="label">fax:</span>04711 / 38 19 47</div>
      <div class="mail">info@korva-talbrunn.de</div>
    </address>
  </section>
</body>
</html>
```